Business Cards

Need business card design that I can update for new employees and details. Needs to incorporate our logo, be bright and fun (in line with tourism and holidays)
Would like a Map of Western Australia on the front with locations all the caravan parks we own (just purchased Tom Price so please include that as well as others listed on our website).
Target Market(s)
Famillies
Contact Information for Business Card
5 Cards -
Neil Perrow (Director) e: perrow@wattlebay.com.au p: 0491 570 156
Mira Perrow (Director) e: perrow@wattlebay.com.au p: 0491 570 157
Owen Halvey (General Manager) e: halvey@wattlebay.com.au p: 0491 570 158
Helen Halvey (General Manager) e: halvey@wattlebay.com.au p: 0491 570 159
Colin Danby (Training and Operations Manager) - e: danby@wattlebay.com.au p:0491 570 110
Colors
Look and feel

```html
<!DOCTYPE html>
<html lang="en">
<head>
<meta charset="utf-8">
<title>Wattle Bay Tourist Parks – Business Card</title>
<link rel="stylesheet" href="https://fonts.googleapis.com/css2?family=Roboto:wght@400;500&family=Roboto+Condensed:wght@500&display=swap">
<style>
  :root {
    --bg: #e9e6e1;
    --card: #f4f4f3;
    --sky: #00b3c4;
    --sea: #3fb39d;
    --teal-text: #18b5c5;
    --sea-text: #36ad9a;
    --ink: #3a3a3a;
    --ink-soft: #555;
  }
  * { box-sizing: border-box; margin: 0; padding: 0; }
  html, body { width: 1200px; height: 800px; overflow: hidden; }
  body {
    background: var(--bg);
    font-family: "Roboto", Arial, sans-serif;
    display: flex;
    align-items: center;
    justify-content: center;
    gap: 40px;
  }
  .card {
    width: 540px;
    height: 310px;
    background: var(--card);
    border-radius: 4px;
    box-shadow: 0 6px 18px rgba(0,0,0,.12);
    position: relative;
    overflow: hidden;
  }

  /* front */
  .card-front .info {
    position: absolute;
    left: 0; top: 0;
    width: 232px; height: 100%;
    padding: 46px 0 0 30px;
  }
  .brand { display: flex; align-items: center; gap: 10px; color: var(--ink); font-weight: 400; }
  .brand-mark { width: 30px; height: 30px; background: var(--sky); flex: none; }
  .brand-name { font-size: 19px; letter-spacing: 2px; text-transform: uppercase; line-height: 1.15; }
  .brand-name small { display: block; font-size: 9.5px; letter-spacing: 3px; }
  .person { margin-top: 52px; }
  .person-name {
    font-family: "Roboto Condensed", Arial, sans-serif;
    font-weight: 500; font-size: 21px; color: var(--teal-text); text-transform: uppercase;
  }
  .person-role {
    font-family: "Roboto Condensed", Arial, sans-serif;
    font-weight: 500; font-size: 13px; color: var(--sea-text); text-transform: uppercase; margin-top: 2px;
  }
  .contacts { list-style: none; margin-top: 22px; font-size: 11.5px; color: var(--ink-soft); }
  .contacts li { display: flex; align-items: center; gap: 7px; margin-bottom: 4px; }
  .contacts svg { width: 10px; height: 10px; fill: var(--teal-text); flex: none; }
  .hero {
    position: absolute; right: 0; top: 0;
    width: 308px; height: 100%;
    background: linear-gradient(180deg, var(--sky) 0%, var(--sky) 48%, var(--sea) 52%, var(--sea) 100%);
  }

  /* back */
  .card-back { display: flex; flex-direction: column; align-items: center; justify-content: center; }
  .card-back .brand { flex-direction: column; gap: 12px; text-align: center; }
  .card-back .brand-mark { width: 64px; height: 64px; }
  .card-back .brand-name { font-size: 22px; }
  .card-back .brand-name small { font-size: 11px; }
  .web { margin-top: 30px; font-size: 13px; letter-spacing: 3px; color: var(--ink-soft); }
</style>
</head>
<body>

  <section class="card card-front">
    <div class="info">
      <div class="brand">
        <span class="brand-mark"></span>
        <span class="brand-name">Wattle Bay<small>Tourist Parks</small></span>
      </div>
      <div class="person">
        <p class="person-name">Neil Perrow</p>
        <p class="person-role">Director</p>
      </div>
      <ul class="contacts">
        <li><svg viewBox="0 0 10 10"><path d="M2 0.5 L3.6 2.6 L2.7 3.6 Q3.6 5.8 6.3 7.3 L7.4 6.4 L9.5 8 L8.3 9.5 Q4.5 9.5 1.5 5.5 Q0 3.3 0.6 1.6 Z"/></svg>0491 570 156</li>
        <li><svg viewBox="0 0 10 10"><path d="M0 2 H10 V8.5 H0 Z M0.6 2.4 L5 5.6 L9.4 2.4" stroke="#f4f4f3" stroke-width=".8"/></svg>perrow@wattlebay.com.au</li>
        <li><svg viewBox="0 0 10 10"><circle cx="5" cy="5" r="4.8"/></svg>www.wattlebay.com.au</li>
      </ul>
    </div>
    <div class="hero" role="img" aria-label="Brand sun rising over a wave with birds, in sky blue and sea green"></div>
  </section>

  <section class="card card-back">
    <div class="brand">
      <span class="brand-mark"></span>
      <span class="brand-name">Wattle Bay<small>Tourist Parks</small></span>
    </div>
    <p class="web">www.wattlebay.com.au</p>
  </section>

</body>
</html>
```